Modern Verdell Tree Care Website

I need a website for a full service Tree Care company. The company provides tree pruning, tree removal, tree preservation, emergency services, stump grinding, and emergency tree services.

Target Market(s)

Customers that need tree services

Industry/Entity Type

Landscaping, Tree Services

Coding

Coded - Design and coding required

Number of Pages Required

5+ page

Font styles to use
Sans Serif

Requirements
Must have
• Good clean design that showcases the services the company provides.
Nice to have
• Services page; contact form, blog, home page, about page

```html
<!DOCTYPE html>
<html lang="en">
<head>
<meta charset="utf-8">
<title>Verdell Tree Care</title>
<link rel="stylesheet" href="https://fonts.googleapis.com/css2?family=Montserrat:wght@300;400;500;600;700;800&display=swap">
<style>
:root{
  --green:#7dc142;
  --green-dark:#5c9c2c;
  --green-deep:#3f6e2a;
  --orange:#f7a934;
  --ink:#2f3133;
  --text:#4a4a4a;
  --beige:#f1f0e6;
  --white:#ffffff;
  --brown:#b9976a;
  --navy:#2c3340;
}
*{box-sizing:border-box;margin:0;padding:0}
html,body{width:1200px;height:4338px;overflow:hidden}
body{position:relative;font-family:'Montserrat',sans-serif;color:var(--text);background:var(--white)}
.abs{position:absolute}
.photo{position:absolute;overflow:hidden}

/* header */
.site-header{position:absolute;left:0;top:0;width:1200px;height:82px;background:var(--white);z-index:5}
.brand{position:absolute;left:86px;top:16px;display:flex;align-items:center;gap:10px}
.brand-square{width:44px;height:44px;background:var(--green)}
.brand-name{font-weight:700;font-size:22px;line-height:1.05;color:var(--ink);letter-spacing:1px;text-transform:uppercase}
.main-nav{position:absolute;left:337px;top:34px;display:flex;font-size:13px;font-weight:500;letter-spacing:1.3px;color:var(--ink)}
.main-nav span{position:relative}
.main-nav .sep{color:#bbb;margin:0 26px}
.main-nav .active{color:var(--green)}
.main-nav .active::after{content:"";position:absolute;left:0;right:0;top:24px;height:2px;background:var(--green)}
.header-phone{position:absolute;left:968px;top:0;width:232px;height:82px;background:var(--green);clip-path:polygon(22px 0,100% 0,100% 100%,0 100%);color:var(--white);font-size:16px;letter-spacing:1px;display:flex;align-items:center;padding-left:50px;gap:10px}
.phone-dot{width:24px;height:24px;border-radius:50%;background:var(--white);display:flex;align-items:center;justify-content:center}

/* hero */
.hero{position:absolute;left:0;top:82px;width:1200px;height:680px;background:linear-gradient(180deg,#c8d6e4 0%,#e4eaf0 55%,#eef1f2 100%)}
.hero-left{left:0;top:0;width:430px;height:640px;background:linear-gradient(160deg,#6f7d3a 0%,#9a9c6d 45%,rgba(200,190,170,.2) 100%)}
.hero-right{left:820px;top:0;width:380px;height:640px;background:linear-gradient(200deg,#8b7a52 0%,#a6925f 40%,rgba(210,200,180,.2) 100%)}
.hero-welcome{position:absolute;top:172px;left:0;width:1170px;display:flex;justify-content:center;align-items:center;gap:12px;font-size:34px;font-weight:300;color:var(--ink);letter-spacing:1px}
.hero-welcome i{display:block;width:88px;height:2px;background:var(--green)}
.hero-title{position:absolute;top:214px;left:0;width:1170px;text-align:center;font-size:54px;line-height:66px;font-weight:800;color:var(--ink);letter-spacing:1px}
.hero-sub{position:absolute;top:290px;left:0;width:1170px;text-align:center;font-size:20px;color:var(--ink)}
.btn{display:inline-flex;align-items:center;justify-content:center;border-radius:30px;background:var(--orange);color:var(--white);font-weight:600;letter-spacing:.8px;text-transform:uppercase}
.hero-btn{position:absolute;left:500px;top:336px;width:163px;height:44px;font-size:13px}
.hero-arrow{position:absolute;top:240px;width:24px;height:40px}

/* about */
.about-frame{left:114px;top:806px;width:416px;height:402px;background:var(--green);padding:10px}
.about-frame .inner{position:absolute;left:10px;top:10px;right:10px;bottom:10px;border:2px solid rgba(255,255,255,.7)}
.about-photo{left:48px;top:34px;width:320px;height:332px;background:linear-gradient(160deg,#5d8f3a 0%,#a5c27a 50%,#e58b3a 75%,#47702e 100%)}
.about-title{position:absolute;left:610px;top:802px;font-size:40px;line-height:42px;font-weight:700;color:var(--ink)}
.about-title span{display:block;font-weight:400;color:var(--green)}
.about-text{position:absolute;left:618px;top:920px;width:508px;font-size:15px;line-height:23px;color:var(--text)}
.about-text p+p{margin-top:23px}
.about-btn{position:absolute;left:614px;top:1152px;width:196px;height:56px;font-size:16px}

/* services */
.services{position:absolute;left:0;top:1237px;width:1200px;height:785px;background:var(--beige)}
.section-title{position:absolute;left:0;width:1200px;text-align:center;font-size:36px;font-weight:700;color:var(--ink);letter-spacing:.5px}
.section-title .light{font-weight:400;color:var(--green)}
.title-rule{position:absolute;height:3px;background:var(--green)}
.card{position:absolute;width:300px;height:215px;border-radius:26px 0 26px 0;overflow:hidden}
.card .img{position:absolute;inset:0}
.card .shade{position:absolute;inset:0;background:linear-gradient(180deg,rgba(0,0,0,0) 45%,rgba(0,0,0,.55) 100%)}
.card h3{position:absolute;left:0;right:0;bottom:28px;text-align:center;color:var(--white);font-size:17px;font-weight:700;letter-spacing:.3px}
.card h3::after{content:"";position:absolute;left:50%;bottom:-10px;width:34px;height:2px;margin-left:-17px;background:var(--white)}
.card.featured{background:var(--green-deep)}
.card.featured .img{opacity:.25}
.card.featured h3{top:40px;bottom:auto}
.card.featured h3::after{display:none}
.card.featured p{position:absolute;left:38px;right:38px;top:74px;color:var(--white);font-size:11px;line-height:16px;text-align:center}
.card.featured .mini{position:absolute;left:93px;top:138px;width:110px;height:26px;border-radius:13px;background:var(--green);color:var(--white);font-size:9px;font-weight:600;display:flex;align-items:center;justify-content:center}

/* why choose */
.why-icon{position:absolute;width:80px;height:80px;border-radius:50%;display:flex;align-items:center;justify-content:center;z-index:3}
.why-icon.g{background:var(--green)}
.why-icon.o{background:var(--orange)}
.why-label{position:absolute;z-index:3;font-size:16px;font-weight:600;color:var(--ink);line-height:20px;text-transform:uppercase}
.tree{left:448px;top:2160px;width:350px;height:310px;border-radius:48% 48% 40% 40%;background:radial-gradient(circle at 50% 40%,#6da63f 0%,#4a7d2b 55%,#2f5a1f 100%)}

/* blogs */
.blogs{position:absolute;left:0;top:2668px;width:1200px;height:745px;background:var(--beige)}
.blogs-title{position:absolute;left:100px;top:2820px;font-size:36px;font-weight:700;color:var(--ink)}
.blogs-title span{font-weight:400;color:var(--orange)}
.blog-big{position:absolute;left:99px;top:2903px;width:474px;height:405px;background:var(--white);border:1px solid #d8d8d0}
.blog-big .img{left:0;top:0;width:472px;height:286px;background:linear-gradient(120deg,#2f5230 0%,#7a6a55 45%,#a49885 100%)}
.date{position:absolute;background:var(--green);color:var(--white);font-weight:600}
.blog-big .date{left:0;top:260px;height:27px;padding:0 24px;font-size:12px;line-height:27px}
.blog-big h4{position:absolute;left:38px;top:302px;width:400px;font-size:18px;line-height:26px;font-weight:500;color:var(--ink)}
.link{position:absolute;color:var(--green);font-weight:600;text-decoration:underline}
.blog-big .link{left:38px;top:362px;font-size:13px}
.blog-sm{position:absolute;left:592px;width:502px;height:194px;background:var(--white);border:1px solid #d8d8d0}
.blog-sm .img{left:0;top:0;width:238px;height:192px}
.blog-sm .date{left:266px;top:38px;height:20px;padding:0 12px;font-size:9px;line-height:20px}
.blog-sm h4{position:absolute;left:264px;top:70px;width:212px;font-size:14px;line-height:19px;font-weight:600;color:var(--ink)}
.blog-sm .link{left:264px;top:136px;font-size:11px}

/* contact */
.contact{position:absolute;left:0;top:3410px;width:1200px;height:680px;background:var(--green)}
.contact-title{position:absolute;left:135px;top:3492px;font-size:36px;font-weight:600;color:var(--white)}
.field{position:absolute;left:140px;width:415px;background:var(--white);display:flex;align-items:center;gap:10px;padding-left:18px;font-size:12px;color:#555}
.field.msg{align-items:flex-start;padding-top:16px}
.send{position:absolute;left:136px;top:3836px;width:170px;height:42px;border-radius:21px;background:var(--navy);color:var(--white);font-size:13px;font-weight:600;letter-spacing:.5px;display:flex;align-items:center;justify-content:center}
.circle-big{left:653px;top:3473px;width:444px;height:444px;border-radius:50%;border:7px solid var(--white);background:linear-gradient(140deg,#cfd8b5 0%,#4e7a30 45%,#2e5220 100%)}
.circle-ring{left:632px;top:3699px;width:260px;height:260px;border-radius:50%;border:6px solid var(--orange)}
.circle-small{left:642px;top:3709px;width:240px;height:240px;border-radius:50%;border:5px solid var(--white);background:linear-gradient(160deg,#7f9c52 0%,#4f7a30 60%,#c7a27a 100%)}

/* footer */
.footer-brand{position:absolute;left:0;top:4030px;width:1200px;display:flex;justify-content:center;align-items:center;gap:12px}
.footer-brand .brand-square{width:56px;height:56px}
.footer-brand .brand-name{font-size:30px}
.footer-rule{position:absolute;left:100px;width:1000px;height:1px;background:#d6d6d6}
.footer-nav{position:absolute;left:0;top:4142px;width:1200px;display:flex;justify-content:center;align-items:center;font-size:14px;font-weight:600;color:var(--ink)}
.footer-nav .dot{width:5px;height:5px;border-radius:50%;background:var(--green);margin:0 30px}
.footer-contacts{position:absolute;left:195px;top:4212px;display:flex;align-items:center;font-size:13px;font-weight:600;color:var(--ink)}
.fc{display:flex;align-items:center;gap:8px;margin-right:50px}
.fc-icon{width:34px;height:34px;border-radius:50%;background:var(--green);display:flex;align-items:center;justify-content:center}
.socials{position:absolute;left:927px;top:4218px;display:flex;gap:12px}
.socials i{display:block;width:24px;height:24px;border-radius:50%;border:2px solid var(--green)}
.copyright{position:absolute;left:0;top:4283px;width:1200px;height:55px;background:var(--brown);color:var(--white);font-size:12px;display:flex;align-items:center;justify-content:center}
</style>
</head>
<body>

<!-- header -->
<header class="site-header">
  <div class="brand"><div class="brand-square"></div><div class="brand-name">Verdell<br>Tree Care</div></div>
  <nav class="main-nav">
    <span class="active">HOME</span><span class="sep">|</span>
    <span>ABOUT US</span><span class="sep">|</span>
    <span>SERVICES</span><span class="sep">|</span>
    <span>BLOG</span><span class="sep">|</span>
    <span>CONTACT US</span>
  </nav>
  <div class="header-phone">
    <span class="phone-dot"><svg width="14" height="14" viewBox="0 0 24 24"><path fill="#7dc142" d="M6.6 10.8a15.1 15.1 0 0 0 6.6 6.6l2.2-2.2c.3-.3.7-.4 1-.2 1.1.4 2.3.6 3.6.6.6 0 1 .4 1 1V20c0 .6-.4 1-1 1C10.6 21 3 13.4 3 4c0-.6.4-1 1-1h3.5c.6 0 1 .4 1 1 0 1.3.2 2.5.6 3.6.1.3 0 .7-.2 1z"/></svg></span>
    (555) 214 7720
  </div>
</header>

<!-- hero -->
<section class="hero">
  <div class="photo hero-left" role="img" aria-label="Arborist in a bucket lift cutting a tree branch"></div>
  <div class="photo hero-right" role="img" aria-label="Climber with a chainsaw cutting tree limbs"></div>
  <svg class="hero-arrow" style="left:28px" viewBox="0 0 24 40"><path d="M20 4 6 20l14 16" fill="none" stroke="#7dc142" stroke-width="3"/></svg>
  <svg class="hero-arrow" style="left:1148px" viewBox="0 0 24 40"><path d="M4 4l14 16L4 36" fill="none" stroke="#fff" stroke-width="3"/></svg>
  <div class="hero-welcome"><i></i>WELCOME TO<i></i></div>
  <h1 class="hero-title">VERDELL TREE CARE</h1>
  <p class="hero-sub">Serving Lafayette and surrounding areas.</p>
  <a class="btn hero-btn">Contact Us</a>
</section>
<svg class="abs" style="left:0;top:650px" width="1200" height="110" viewBox="0 0 1200 110">
  <path d="M0 95 Q600 -45 1200 95 V110 H0Z" fill="#fff"/>
  <path d="M0 95 Q600 -45 1200 95" fill="none" stroke="#7dc142" stroke-width="7"/>
</svg>

<!-- about -->
<div class="photo about-frame">
  <div class="inner"></div>
  <div class="photo about-photo" role="img" aria-label="Arborist in orange shirt climbing among tree branches"></div>
</div>
<h2 class="about-title">ABOUT VERDELL<span>TREE CARE</span></h2>
<div class="about-text">
  <p>At Verdell Tree Care, we are more than just a tree service company, we are stewards of our beautiful trees. With a passion deeply rooted in arboriculture, we embark on a mission to promote the health, beauty, and safety of your trees and landscapes.</p>
  <p>Whether it's expert tree trimming to enhance aesthetics, meticulous tree removal to mitigate hazards, or comprehensive tree health assessments to ensure safety, we approach each task with unwavering dedication and attention to detail.</p>
</div>
<a class="btn about-btn">Learn More</a>

<!-- services -->
<section class="services"></section>
<svg class="abs" style="left:0;top:1232px" width="1200" height="80" viewBox="0 0 1200 80">
  <path d="M0 0 H1200 V8 Q600 140 0 8Z" fill="#fff"/>
  <path d="M0 8 Q600 140 1200 8" fill="none" stroke="#f7a934" stroke-width="6"/>
</svg>
<h2 class="section-title" style="top:1388px">SERVICES <span class="light">PROVIDE</span></h2>
<div class="title-rule" style="left:575px;top:1440px;width:50px"></div>

<div class="card" style="left:120px;top:1476px"><div class="img" role="img" aria-label="Pruning shears cutting a branch" style="background:linear-gradient(150deg,#8fb35c,#5b7d36 60%,#c7c0a8)"></div><div class="shade"></div><h3>TREE PRUNING</h3></div>
<div class="card featured" style="left:446px;top:1476px"><div class="img" role="img" aria-label="Tree removal work" style="background:linear-gradient(150deg,#6b8f4a,#2e4a22)"></div><h3>TREE REMOVAL</h3><p>Lorem ipsum dolor sit amet, consectetur adipiscing elit, sed do eiusmod tempor incididunt ut labore et dolore</p><span class="mini">LEARN MORE</span></div>
<div class="card" style="left:773px;top:1476px"><div class="img" role="img" aria-label="Shovel planting a young tree in soil" style="background:linear-gradient(160deg,#7aa846,#5a3f2a 55%,#4a7a2a)"></div><div class="shade"></div><h3>TREE PRESERVATION</h3></div>
<div class="card" style="left:117px;top:1715px"><div class="img" role="img" aria-label="Stump grinder working on a tree stump" style="background:linear-gradient(160deg,#4d6e3a,#9b6a43 55%,#6a4a30)"></div><div class="shade"></div><h3>STUMP GRINDING</h3></div>
<div class="card" style="left:444px;top:1715px"><div class="img" role="img" aria-label="Fallen tree on a house after a storm" style="background:linear-gradient(160deg,#6f8a52,#8e8470 55%,#4d6a36)"></div><div class="shade"></div><h3>TREE EMERGENCY SERVICES</h3></div>
<div class="card" style="left:771px;top:1715px"><div class="img" role="img" aria-label="Arborist with ropes climbing a tree trunk" style="background:linear-gradient(160deg,#6e9ac8,#8a7a5a 50%,#d9783a 70%,#4a6a30)"></div><div class="shade"></div><h3>CABLING &amp; BRACING</h3></div>

<!-- why choose -->
<h2 class="section-title" style="top:2100px">WHY CHOOSE <span class="light">VERDELL</span></h2>
<div class="title-rule" style="left:580px;top:2148px;width:54px"></div>
<svg class="abs" style="left:330px;top:2200px" width="540" height="410" viewBox="0 0 540 410">
  <path d="M40 30 A262 262 0 0 0 500 310 M500 310 A262 262 0 0 0 500 30" fill="none" stroke="#f7c37a" stroke-width="1.5"/>
</svg>
<div class="photo tree" role="img" aria-label="Large green leafy tree"></div>

<div class="why-icon g" style="left:332px;top:2170px"><svg width="40" height="40" viewBox="0 0 24 24" fill="none" stroke="#fff" stroke-width="1.4"><path d="M6 3h9l3 3v15H6z"/><path d="M9 13l2 2 4-4"/></svg></div>
<div class="why-label" style="left:150px;top:2188px;width:160px;text-align:right">Licensed and<br>Insured</div>

<div class="why-icon o" style="left:307px;top:2325px"><svg width="40" height="40" viewBox="0 0 24 24" fill="none" stroke="#fff" stroke-width="1.4"><circle cx="12" cy="12" r="8"/><path d="M12 7v5l3 2"/></svg></div>
<div class="why-label" style="left:80px;top:2352px;width:213px;text-align:right">24 Hour Emergency<br>Services</div>

<div class="why-icon g" style="left:374px;top:2475px"><svg width="40" height="40" viewBox="0 0 24 24" fill="none" stroke="#fff" stroke-width="1.4"><path d="M12 21s-6-6-6-11a6 6 0 0 1 12 0c0 5-6 11-6 11z"/><circle cx="12" cy="10" r="2"/></svg></div>
<div class="why-label" style="left:180px;top:2508px;width:180px;text-align:right">Locally Owned<br>&amp; Operated</div>

<div class="why-icon o" style="left:552px;top:2554px"><svg width="40" height="40" viewBox="0 0 24 24" fill="none" stroke="#fff" stroke-width="1.4"><circle cx="12" cy="8" r="3"/><circle cx="6" cy="11" r="2"/><circle cx="18" cy="11" r="2"/><path d="M6 19a6 6 0 0 1 12 0M2 19a4 4 0 0 1 4-4M22 19a4 4 0 0 0-4-4"/></svg></div>
<div class="why-label" style="left:450px;top:2646px;width:300px;text-align:center">Licensed Arborist<br>on Staff</div>

<div class="why-icon g" style="left:761px;top:2481px"><svg width="40" height="40" viewBox="0 0 24 24" fill="none" stroke="#fff" stroke-width="1.4"><path d="M6 4h12v16H6z"/><path d="M9 8h6M9 12h6M9 16h4"/></svg></div>
<div class="why-label" style="left:852px;top:2518px">Free Estimate</div>

<div class="why-icon o" style="left:817px;top:2328px"><svg width="40" height="40" viewBox="0 0 24 24" fill="none" stroke="#fff" stroke-width="1.4"><path d="M5 12a7 7 0 0 1 14 0z"/><path d="M4 12h16M12 5v3"/><path d="M7 15a5 5 0 0 0 10 0"/></svg></div>
<div class="why-label" style="left:911px;top:2346px">Safety is our<br>top priority</div>

<div class="why-icon g" style="left:791px;top:2175px"><svg width="40" height="40" viewBox="0 0 24 24" fill="none" stroke="#fff" stroke-width="1.4"><circle cx="12" cy="9" r="6"/><path d="M12 9v12M9 21h6"/></svg></div>
<div class="why-label" style="left:885px;top:2196px">Professional<br>Work</div>

<!-- blogs -->
<section class="blogs"></section>
<svg class="abs" style="left:0;top:2664px" width="1200" height="110" viewBox="0 0 1200 110">
  <path d="M0 0 H1200 V6 Q600 190 0 6Z" fill="#fff"/>
  <path d="M0 6 Q600 190 1200 6" fill="none" stroke="#7dc142" stroke-width="7"/>
</svg>
<h2 class="blogs-title">LATEST <span>BLOGS</span></h2>
<div class="title-rule" style="left:100px;top:2870px;width:58px"></div>

<article class="blog-big">
  <div class="photo img" role="img" aria-label="Chainsaw cutting into a large tree trunk"></div>
  <span class="date">20 MAY 2024</span>
  <h4>Lorem ipsum dolor sit amet consectetur adipiscing elit sed do eiusmod</h4>
  <a class="link">LEARN MORE</a>
</article>
<article class="blog-sm" style="top:2903px">
  <div class="photo img" role="img" aria-label="Arborist harnessed while climbing a tree" style="background:linear-gradient(150deg,#c9d3c0,#6d7f55 55%,#3f5430)"></div>
  <span class="date">20 MAY 2024</span>
  <h4>Lorem ipsum dolor sit amet consectetur adipiscing elit sed do eiusmod</h4>
  <a class="link">LEARN MORE</a>
</article>
<article class="blog-sm" style="top:3115px">
  <div class="photo img" role="img" aria-label="Gardener trimming branches with long loppers" style="background:linear-gradient(150deg,#6a8a4a,#b9c7a4 55%,#5a7a3a)"></div>
  <span class="date">10 MAY 2024</span>
  <h4>Lorem ipsum dolor sit amet consectetur adipiscing elit sed do eiusmod</h4>
  <a class="link">LEARN MORE</a>
</article>

<!-- contact -->
<section class="contact"></section>
<h2 class="contact-title">CONTACT US</h2>
<div class="field" style="top:3568px;height:42px"><svg width="12" height="12" viewBox="0 0 24 24"><circle cx="12" cy="8" r="5" fill="#888"/><path d="M3 22a9 9 0 0 1 18 0z" fill="#888"/></svg>Name*</div>
<div class="field" style="top:3624px;height:42px"><svg width="12" height="12" viewBox="0 0 24 24"><rect x="2" y="5" width="20" height="14" fill="none" stroke="#888" stroke-width="2"/><path d="M2 5l10 8 10-8" fill="none" stroke="#888" stroke-width="2"/></svg>Email address*</div>
<div class="field" style="top:3678px;height:42px"><svg width="12" height="12" viewBox="0 0 24 24"><path fill="#888" d="M6.6 10.8a15.1 15.1 0 0 0 6.6 6.6l2.2-2.2c.3-.3.7-.4 1-.2 1.1.4 2.3.6 3.6.6.6 0 1 .4 1 1V20c0 .6-.4 1-1 1C10.6 21 3 13.4 3 4c0-.6.4-1 1-1h3.5c.6 0 1 .4 1 1 0 1.3.2 2.5.6 3.6.1.3 0 .7-.2 1z"/></svg>Phone number*</div>
<div class="field msg" style="top:3732px;height:88px"><svg width="12" height="12" viewBox="0 0 24 24"><path fill="#888" d="M3 4h18v12H8l-5 4z"/></svg>Leave Message</div>
<a class="send">SEND MESSAGE</a>
<div class="photo circle-big" role="img" aria-label="Hedge shears trimming a green hedge"></div>
<div class="abs circle-ring"></div>
<div class="photo circle-small" role="img" aria-label="Gardener trimming a hedge with a power trimmer"></div>

<!-- footer -->
<svg class="abs" style="left:0;top:3970px" width="1200" height="120" viewBox="0 0 1200 120">
  <path d="M0 100 Q600 -80 1200 100 V120 H0Z" fill="#fff"/>
  <path d="M0 100 Q600 -80 1200 100" fill="none" stroke="#f7a934" stroke-width="6"/>
</svg>
<div class="abs" style="left:0;top:4088px;width:1200px;height:200px;background:#fff"></div>
<div class="footer-brand"><div class="brand-square"></div><div class="brand-name">Verdell<br>Tree Care</div></div>
<div class="footer-rule" style="top:4117px"></div>
<nav class="footer-nav">
  <span>HOME</span><i class="dot"></i><span>ABOUT US</span><i class="dot"></i><span>SERVICES</span><i class="dot"></i><span>BLOGS</span><i class="dot"></i><span>REVIEWS</span><i class="dot"></i><span>CONTACT</span>
</nav>
<div class="footer-rule" style="top:4186px"></div>
<div class="footer-contacts">
  <div class="fc"><span class="fc-icon"><svg width="16" height="16" viewBox="0 0 24 24"><path fill="#fff" d="M6.6 10.8a15.1 15.1 0 0 0 6.6 6.6l2.2-2.2c.3-.3.7-.4 1-.2 1.1.4 2.3.6 3.6.6.6 0 1 .4 1 1V20c0 .6-.4 1-1 1C10.6 21 3 13.4 3 4c0-.6.4-1 1-1h3.5c.6 0 1 .4 1 1 0 1.3.2 2.5.6 3.6.1.3 0 .7-.2 1z"/></svg></span>(555) 214-7720</div>
  <div class="fc"><span class="fc-icon"><svg width="16" height="16" viewBox="0 0 24 24"><path fill="#fff" d="M6.6 10.8a15.1 15.1 0 0 0 6.6 6.6l2.2-2.2c.3-.3.7-.4 1-.2 1.1.4 2.3.6 3.6.6.6 0 1 .4 1 1V20c0 .6-.4 1-1 1C10.6 21 3 13.4 3 4c0-.6.4-1 1-1h3.5c.6 0 1 .4 1 1 0 1.3.2 2.5.6 3.6.1.3 0 .7-.2 1z"/></svg></span>(555) 309-4418</div>
  <div class="fc"><span class="fc-icon"><svg width="16" height="16" viewBox="0 0 24 24"><rect x="3" y="6" width="18" height="12" fill="none" stroke="#fff" stroke-width="2"/><path d="M3 6l9 7 9-7" fill="none" stroke="#fff" stroke-width="2"/></svg></span>hello@verdelltreecare.com</div>
</div>
<div class="socials"><i></i><i></i><i></i><i></i></div>
<div class="copyright">Copyright © 2024 Verdell Tree Care | All Right Reserved</div>

</body>
</html>
```